an A3 Folded in half to A4 brochure for strata management company

Color scheme must match logo and website. Must have pictures that deliver the meaning of the wording part. Please refer to the flyer artwork enclosed. Contents are provided as enclosed.

Target Market(s)

Developers or strata title property owners

Industry/Entity Type

It Company

Font styles to use
Serif

Requirements
Must have
• 1) professional layout, simple and easy to read
• 2) Have relevant pictures such as building and people to deliver the meaning of the wording part. Please refer to the flier artwork enclosed.
• I.e. Service for developer, has people's picture of developer looking.
• 3) The brochure should work as a 24/7 marketer to promote the business rather than a nice picture and cannot get viewers to pick up the phone.
• 4) please make the color theme warm
• 5) should have clear call for action
Should not have
• Please do not make it too colorful which will distract people.

```html
<!DOCTYPE html>
<html lang="en">
<head>
<meta charset="utf-8">
<title>Urbancrest Strata – Introduction</title>
<link href="https://fonts.googleapis.com/css2?family=Source+Sans+3:wght@400;600;700&display=swap" rel="stylesheet">
<style>
  :root {
    --paper-top: #fdebc9;
    --paper-bottom: #fbdccd;
    --brand-orange: #e8552b;
    --brand-red: #e52421;
    --brand-amber: #f6a51b;
    --ink: #1f1f1f;
    --white: #ffffff;
    --scene-light: #dfe6f5;
    --scene-deep: #6f86c4;
  }
  * { margin: 0; padding: 0; box-sizing: border-box; }
  html, body { width: 848px; height: 1200px; overflow: hidden; }
  body {
    font-family: "Source Sans 3", "Myriad Pro", "Helvetica Neue", Arial, sans-serif;
    color: var(--ink);
  }
  .page {
    position: relative;
    width: 848px;
    height: 1200px;
    overflow: hidden;
    background: linear-gradient(180deg, var(--paper-top) 0%, #fde3cc 55%, var(--paper-bottom) 100%);
  }
  .section-mark {
    position: absolute;
    left: 35px; top: 50px;
    width: 77px; height: 77px;
    border-radius: 50%;
    background: var(--brand-orange);
    z-index: 2;
  }
  .section-banner {
    position: absolute;
    left: 104px; top: 70px;
    width: 244px; height: 36px;
    background: var(--brand-orange);
    border-radius: 0 3px 3px 0;
    color: var(--white);
    font-weight: 700;
    font-size: 33px;
    line-height: 36px;
    padding-left: 22px;
    z-index: 3;
  }
  .lead {
    position: absolute;
    left: 74px; top: 131px;
    width: 700px;
    color: var(--brand-red);
    font-size: 16.2px;
    line-height: 18.5px;
    white-space: nowrap;
  }
  .intro-body {
    position: absolute;
    left: 74px; top: 205px;
    width: 700px;
    font-size: 16.2px;
    line-height: 18.5px;
  }
  .intro-body .line {
    display: block;
    text-align: justify;
    text-align-last: justify;
  }
  .intro-body .line:last-child { text-align-last: left; }
  .why-heading {
    position: absolute;
    left: 74px; top: 294px;
    color: var(--brand-red);
    font-size: 25px;
    font-weight: 700;
  }
  .scene {
    position: absolute;
    left: 604px; top: 728px;
    width: 244px; height: 472px;
    background: linear-gradient(180deg, var(--scene-light) 0%, var(--scene-deep) 100%);
  }
  .reasons { list-style: none; }
  .reason {
    position: absolute;
    left: 112px;
    font-size: 15.6px;
    line-height: 18.5px;
    padding-left: 39px;
    white-space: nowrap;
  }
  .reason::before {
    content: "";
    position: absolute;
    left: 0; top: 2px;
    width: 12px; height: 12px;
    border-radius: 50%;
    background: var(--brand-amber);
  }
</style>
</head>
<body>
<main class="page">
  <div class="section-mark" aria-hidden="true"></div>
  <h1 class="section-banner">Introduction</h1>

  <p class="lead">UrbanCrest strata management is a boutique strata business catering for the proprietor/s looking for<br>a better way to manage your complex. Our staff has over 35 years’ experience in the industry and<br>keep themselves updated with changes to new strata laws as they are introduced.</p>

  <p class="intro-body">
    <span class="line">We know how important it is for you to make sure your complex is always well maintained therefore</span>
    <span class="line">we place importance on prompt customer service and making sure, your maintenance is attended</span>
    <span class="line">in a quick and timely manner. We also use only licensed and professional tradespeople who</span>
    <span class="line">guarantee all repairs.</span>
  </p>

  <h2 class="why-heading">Why Urbancrest</h2>

  <div class="scene" role="img" aria-label="Illustration area: city office towers with a tradesman holding a wrench"></div>

  <ul class="reasons">
    <li class="reason" style="top:344px">We respect people no matter their cultural background. We are a multicultural<br>company and our staff are able to communicate in a number of languages as well as<br>English. We will support your correct entitlements with respect and fairness</li>
    <li class="reason" style="top:418px">At Urbancrest strata we have a commitment to ensure that all repairs and maintenance is<br>attended to ASAP. We have an excellent after hours service which can be reached when<br>the office is closed by just phoning our office number and you will be automatically<br>transferred through to our tradesman.</li>
    <li class="reason" style="top:510px">Management fee: our management fee includes costs for emails, photo copying, faxes,<br>postage costs and phone calls. We also use the ledgerline computer system which<br>provides owners with all their information requirements 24/7.</li>
    <li class="reason" style="top:585px">UrbanCrest understands owners corporations are concerned with costs of maintenance<br>etc and we are committed to provide tradesman who will undertake repairs at the best<br>price while maintaining the highest quality repairs and service. All work is guaranteed for<br>a reasonable time.</li>
    <li class="reason" style="top:677px">Response times: our office is open 9am to 5pm Monday to Friday. A Staff member will<br>reply to your phone calls within one hour, voice mail within 3 hours<br>and written correspondence on the same day.</li>
    <li class="reason" style="top:751px">After hours emergency service: residents only need to phone<br>our office and they will be automatically transferred to an<br>after hours tradesman who will arrange repairs.</li>
    <li class="reason" style="top:826px">Regularly visit all our buildings to check for repairs and<br>maintenance and all breaches of by-laws.</li>
    <li class="reason" style="top:881px">Efficient communication. We recommend<br>regular communication with the<br>Executive Committee and we also<br>are able to organise electronic<br>communication with owners<br>which is cost effective and quick.</li>
    <li class="reason" style="top:1011px">We use only fully licensed and<br>experienced tradesmen who<br>guarantee all their work.</li>
  </ul>
</main>
</body>
</html>
```